Business Card Design for Marketing Firm

Looking for business card design for higher end marketing firm. Clean but impressionable/trendy. We are a marketing firm that represents manufacturers in the foodservice equipment and supply industry. Our customers are end users such has hotels, restaurants, country clubs, convention centers and casinos as well as distributors of restaurants supplies and equipment, and manufacturers of foodservice equipment and supplies.
Target Market(s)
Hotels, Restaurants, Supply & Equipment Distributors, Foodservice Manufacturers
Industry/Entity Type
Foodservice/Hospitality
Contact Information for Business Card
Name, Title, Contact Number, Email, Website, Social Media, Address
Requirements
Must have
- Clean & Simple but Serious and Impressionable

```html
<!DOCTYPE html>
<html lang="en">
<head>
<meta charset="utf-8">
<title>Corvale Partners – Business Card</title>
<link rel="stylesheet" href="https://fonts.googleapis.com/css2?family=Montserrat:wght@500;700;800&family=Open+Sans:wght@400&display=swap">
<style>
  :root {
    --navy: #2a2a78;
    --white: #ffffff;
    --backdrop: #ecebe8;
  }
  * { margin: 0; padding: 0; box-sizing: border-box; }
  html, body { width: 1200px; height: 834px; overflow: hidden; }
  body { background: var(--backdrop); position: relative; font-family: "Open Sans", sans-serif; }

  .card {
    position: absolute; top: 268px; width: 520px; height: 297px;
    border-radius: 26px; overflow: hidden;
    box-shadow: 0 14px 30px rgba(0,0,0,.18);
  }
  .card--front { left: 50px; background: var(--white); }
  .card--back { left: 630px; background: var(--navy); }

  .card__shapes { position: absolute; inset: 0; }

  .brand {
    position: absolute; display: flex; align-items: center;
    font-family: "Montserrat", sans-serif; font-weight: 700; white-space: nowrap;
  }
  .brand__dot { border-radius: 50%; flex: none; }
  .card--front .brand { left: 92px; top: 42px; color: var(--navy); font-size: 20px; gap: 10px; }
  .card--front .brand__dot { width: 12px; height: 12px; background: var(--navy); }
  .card--back .brand { left: 0; right: 0; justify-content: center; top: 122px; color: var(--white); font-size: 32px; gap: 14px; }
  .card--back .brand__dot { width: 18px; height: 18px; background: var(--white); }

  .contact { position: absolute; left: 24px; top: 140px; color: var(--white); font-size: 11.5px; list-style: none; }
  .contact li { display: flex; align-items: center; gap: 7px; height: 18px; }
  .contact svg { width: 10px; height: 10px; fill: var(--white); flex: none; }

  .person { position: absolute; right: 28px; top: 120px; color: var(--navy); }
  .person__name { font-family: "Montserrat", sans-serif; font-weight: 800; font-size: 19px; letter-spacing: .5px; }
  .person__title { font-family: "Montserrat", sans-serif; font-weight: 500; font-size: 13px; letter-spacing: .6px; }

  .address { position: absolute; left: 250px; top: 238px; color: var(--white); font-size: 12.5px; line-height: 1.45; text-align: right; width: 150px; }

  .social { position: absolute; left: 0; right: 0; top: 190px; display: flex; justify-content: center; gap: 6px; }
  .social span { width: 13px; height: 13px; border: 1.2px solid var(--white); border-radius: 50%; display: block; }
</style>
</head>
<body>

  <section class="card card--front" aria-label="Business card front">
    <svg class="card__shapes" viewBox="0 0 520 297" preserveAspectRatio="none" aria-hidden="true">
      <path d="M0,104 C190,112 380,170 520,256 L520,297 L0,297 Z" fill="var(--navy)"/>
      <path d="M0,118 C190,126 380,184 520,270" fill="none" stroke="var(--white)" stroke-width="4"/>
    </svg>

    <div class="brand"><span class="brand__dot"></span>Corvale Partners</div>

    <ul class="contact">
      <li><svg viewBox="0 0 10 10"><path d="M2 0.5 L3.6 2.6 L2.8 3.6 C3.4 5 4.8 6.4 6.2 7.1 L7.2 6.3 L9.4 7.9 L8.4 9.5 C4.5 9.4 0.6 5.5 0.5 1.5 Z"/></svg>555 014 2233</li>
      <li><svg viewBox="0 0 10 10"><path d="M2.5 0 H7.5 V10 H2.5 Z M3.5 1 V8 H6.5 V1 Z" fill-rule="evenodd"/></svg>555 018 4400</li>
      <li><svg viewBox="0 0 10 10"><path d="M0 2 H10 V8.5 H0 Z M0.8 2.6 L5 5.6 L9.2 2.6 Z" fill-rule="evenodd"/></svg>info@corvalepartners.com</li>
      <li><svg viewBox="0 0 10 10"><circle cx="5" cy="5" r="4.6"/></svg>www.corvalepartners.com</li>
    </ul>

    <div class="person">
      <div class="person__name">DANIEL HART</div>
      <div class="person__title">Managing Director</div>
    </div>

    <div class="address">Your address, City<br>State, Zip 1234</div>
  </section>

  <section class="card card--back" aria-label="Business card back">
    <div class="brand"><span class="brand__dot"></span>Corvale Partners</div>
    <div class="social" aria-label="Social media links">
      <span></span><span></span><span></span><span></span><span></span>
    </div>
  </section>

</body>
</html>
```